IT Company Business Card Design w/Stationary Design

We have a great logo we like! We are looking to redesign our business cards and all company logo'd merchandise/materials.

We are an IT Company located near the Bay Area (San Francisco, CA). We specialize in Managed Services and offer complete IT Computer and Network Support to Businesses of all sizes. We thrive on making a lasting impression. We have been doing IT for 15yrs+ but are young at heart. We like to stand out and be different. We want to be unique and have a recognizable brand. We need our logo to represent who we are. We are young, professional, creative and outstanding. We don't want to blend in, we want to stand out. Our business card needs to stand out and grab attention. Something Bold, yet simple and clean. (I will provide ideas of what we like to give a taste of what we are looking for).

The design can include any kind of texture/artistic design or sizing EXCEPT please "no square card designs" as they don't seem to fit in wallets very well. We dont mind curved edges, rounded corners, vertical layouts or horizontal layouts, embossing, letter press or raised surfaces. Again, we dont want to look average or plain or boring. :) Be creative - yet practical! We have ordered from ZEPLA designs before and been very happy. Their card sizes tend to be a little different, so beware. Hope this helps!

Target Market(s)

Businesses - Small to Medium, Corporations, Publicly Traded Companies

Industry/Entity Type

Business

Contact Information for Business Card

Harbor Lantern IT
7158 Delacroix Avenue
Suite K
Modesto, CA 95871

Office 209.555.0173
Direct 209.555.0148
Cell 209.555.0196

Dale Pruitt
Founder, CEO
www.hlxq.com
dpruitt@hlxq.com

Locations Serviced: Modesto, Stockton, Pleasanton, Fresno (incorporate this on the card ONLY if there's a good place to do so).

What we specialize in: Computer, Network, Voice, Data. (IT Services)

Our Logo Colors: Black and Blue (#006699). Open to using grey or orange as well - but not required. Don't want too busy....

Logo Font: "Cinthe" (Will attach logo font). We want type style to be clean. You can show different font types including our logo font - and we are open to other font ideas.

The logo can be separated. You can use elements together or apart. Surprise us! :) We "REALLY" want the "hl" to be our identifier/our brand people recognize.

Font styles to use
Sans Serif

Colors
0355a3
3176b5
f37122
f78f20
faa54b
474747
aaaaaa
757575
000000

Requirements
Must have
• Bold, Big, Colorful, Modern/yet Fun, Clean Design, Stand Out Presence, Texture would be welcomed - but not necessary, Card design shape can include cut corners or rounded or square edges. Be creative. (HOWEVER, we don't want a square design because we have found it doesn't fit in wallets that easily).
• We do like using ZEPLA printing company (Which they have particular sizing on their card templates - beware), but are open to other design templates/printing companies as well. We just want to make sure its easy to find a print company to do our work. Too unique could be costly and hard to get cards printed.
• Colors to use: Our logo Blue (#006699), with either whites, grays, black, shades of our blue, and maybe a pinch of orange if needed. Primarily, blue, white, gray or black.
Nice to have
• Texture would be cool or little different edging or shape - but nothing too costly to print. I have seen cards with 3 sharp edges and one round edge. Something like that would be cool as an option. Or a vertical card.
• I love a faded watermark look. It would be nice to see some shading of our circle logo on a few designs. The circle with "hl" in it OR.... taking just the "hl" and using it alone.
Should not have
• No square card designs. Nothing too expensive or elaborate to print. No busy fonts. Do not like Times New Roman type fonts (too old looking). Not a lot of orange (if you even choose to use some orange).

```html
<!DOCTYPE html>
<html lang="en">
<head>
<meta charset="utf-8">
<title>Harbor Lantern IT – Business Card</title>
<link rel="stylesheet" href="https://fonts.googleapis.com/css2?family=Jura:wght@600&family=Didact+Gothic&display=swap">
<style>
  :root {
    --brand-blue: #1f84c0;
    --ink-grey: #474747;
    --muted-grey: #757575;
    --card-white: #ffffff;
    --backdrop: #d4d4d4;
  }
  * { margin: 0; padding: 0; box-sizing: border-box; }
  html, body {
    width: 1200px; height: 907px; overflow: hidden;
    background: var(--backdrop);
  }
  .stage { position: relative; width: 1200px; height: 907px; }
  .card {
    position: absolute; left: 300px; width: 600px; height: 343px;
    background: var(--card-white); border-radius: 14px; overflow: hidden;
  }
  .card--front { top: 92px; }
  .card--back { top: 471px; }

  .holder-name {
    position: absolute; left: 27px; top: 42px;
    font: 600 19px/1 "Jura", sans-serif; letter-spacing: 1.5px;
    color: var(--brand-blue);
  }
  .holder-title {
    position: absolute; left: 27px; top: 69px;
    font: 600 15px/1 "Jura", sans-serif; letter-spacing: 1.5px;
    color: var(--muted-grey);
  }
  .address {
    position: absolute; left: 27px; top: 112px;
    font: 15px/24px "Didact Gothic", sans-serif; color: var(--ink-grey);
    font-style: normal;
  }
  .contact-list {
    position: absolute; left: 27px; top: 197px; list-style: none;
    font: 15px/25.5px "Didact Gothic", sans-serif; color: var(--ink-grey);
  }
  .contact-list li { display: flex; align-items: center; gap: 7px; }
  .contact-list svg { width: 13px; height: 13px; fill: var(--brand-blue); flex: none; }

  .front-mark-block {
    position: absolute; left: 326px; top: 120px; width: 160px; height: 160px;
    background: var(--brand-blue);
  }
  .front-mark-name {
    position: absolute; left: 290px; width: 300px; top: 296px; text-align: center;
    font: 600 30px/1 "Jura", sans-serif; letter-spacing: 1px;
    color: var(--brand-blue); white-space: nowrap;
  }

  .brand-dot {
    position: absolute; left: 254px; top: 84px; width: 92px; height: 92px;
    border-radius: 50%; background: var(--brand-blue);
  }
  .brand-name {
    position: absolute; left: 0; right: 0; top: 208px; text-align: center;
    font: 600 32px/1 "Jura", sans-serif; letter-spacing: 2px;
    color: var(--brand-blue); white-space: nowrap;
  }
</style>
</head>
<body>
<main class="stage">
  <section class="card card--front">
    <h1 class="holder-name">Dale Pruitt</h1>
    <p class="holder-title">Founder, CEO</p>
    <address class="address">
      Harbor Lantern IT<br>
      7158 Delacroix Avenue<br>
      Suite K Modesto, CA 95871
    </address>
    <ul class="contact-list">
      <li><svg viewBox="0 0 16 16" aria-hidden="true"><path d="M1 5c0-2 3-3 7-3s7 1 7 3v1h-4V5H5v1H1z"/><path d="M3 8l2-2h6l2 2v6H3z"/></svg>209.555.0173</li>
      <li><svg viewBox="0 0 16 16" aria-hidden="true"><path d="M4 1l3 3-2 2c1 2 3 4 5 5l2-2 3 3-2 3C7 15 1 9 1 3z"/></svg>209.555.0148</li>
      <li><svg viewBox="0 0 16 16" aria-hidden="true"><path d="M4 0h8a1 1 0 0 1 1 1v14a1 1 0 0 1-1 1H4a1 1 0 0 1-1-1V1a1 1 0 0 1 1-1zm1 2v10h6V2z"/></svg>209.555.0196</li>
      <li><svg viewBox="0 0 16 16" aria-hidden="true"><path d="M0 3h16v1L8 9 0 4z"/><path d="M0 6l8 5 8-5v7H0z"/></svg>dpruitt@hlxq.com</li>
      <li><svg viewBox="0 0 16 16" aria-hidden="true"><path d="M8 0a8 8 0 1 0 0 16A8 8 0 0 0 8 0zm0 1.5c.8 0 1.8 2 2 5H6c.2-3 1.2-5 2-5zM4.5 6.5h-3a6.5 6.5 0 0 1 4-4.6c-.6 1.2-1 2.8-1 4.6zm7 0c0-1.8-.4-3.4-1-4.6a6.5 6.5 0 0 1 4 4.6zM1.5 8h3c0 1.8.4 3.6 1 4.8A6.5 6.5 0 0 1 1.5 8zm4.5 0h4c-.2 3-1.2 6.5-2 6.5S6.2 11 6 8zm5.5 0h3a6.5 6.5 0 0 1-4 4.8c.6-1.2 1-3 1-4.8z"/></svg>www.hlxq.com</li>
    </ul>
    <div class="front-mark-block" aria-hidden="true"></div>
    <p class="front-mark-name">Harbor Lantern</p>
  </section>

  <section class="card card--back">
    <div class="brand-dot" aria-hidden="true"></div>
    <p class="brand-name">Harbor Lantern</p>
  </section>
</main>
</body>
</html>
```